Local Roofing/Construction company business needs new biz card design

We need a new business card design, current cards are from the start of this operation and generic at best. We are a local Construction Company (General Contractor) with a majority of our work originating from insurance claims-exterior finish work is the main focus (Roofs-Siding-Gutters etc). Heavily involved with homeowners and the low ball offers they receive from insurance company's after a insurable event takes place. I have attached some of our original logo file(s) below.

```html
<!DOCTYPE html>
<html lang="en">
<head>
<meta charset="utf-8">
<title>Harlow Builders – Business Card</title>
<link href="https://fonts.googleapis.com/css2?family=Montserrat:wght@400;500;700;800&display=swap" rel="stylesheet">
<style>
  :root {
    --bg-top: #d2d2d2;
    --bg-bottom: #a8a8a8;
    --card: #0f1d21;
    --card-deep: #0c181b;
    --green: #5cbf6e;
    --white: #f2f4f3;
    --pattern: #1a2d32;
  }
  * { margin: 0; padding: 0; box-sizing: border-box; }
  html, body { width: 1200px; height: 802px; overflow: hidden; }
  body {
    background: linear-gradient(180deg, var(--bg-top), var(--bg-bottom));
    font-family: "Montserrat", sans-serif;
    position: relative;
  }
  .card {
    position: absolute;
    top: 246px;
    width: 540px;
    height: 310px;
    border-radius: 22px;
    background: var(--card);
    border-bottom: 4px solid var(--green);
    box-shadow: 0 14px 30px rgba(0,0,0,0.35);
    overflow: hidden;
  }
  .card-front { left: 40px; }
  .card-back { left: 620px; }

  .brand {
    position: absolute;
    top: 46px;
    left: 50%;
    transform: translateX(-50%);
    display: flex;
    align-items: center;
    gap: 12px;
    white-space: nowrap;
  }
  .brand-mark {
    width: 34px; height: 34px;
    background: var(--green);
    border-radius: 6px;
  }
  .brand-name {
    color: var(--green);
    font-weight: 800;
    font-size: 30px;
    letter-spacing: 1px;
  }

  .details {
    position: absolute;
    top: 128px;
    left: 0; right: 0;
    display: flex;
    justify-content: center;
    align-items: center;
    gap: 22px;
  }
  .person { text-align: right; }
  .person-name {
    color: var(--green);
    font-weight: 700;
    font-size: 21px;
    letter-spacing: 1px;
  }
  .person-role {
    color: var(--white);
    font-size: 14px;
    margin-top: 2px;
  }
  .divider {
    width: 1px;
    height: 66px;
    background: var(--green);
  }
  .contacts { list-style: none; }
  .contacts li {
    color: var(--white);
    font-size: 13px;
    display: flex;
    align-items: center;
    gap: 8px;
    line-height: 22px;
  }
  .contacts svg { width: 11px; height: 11px; fill: var(--green); flex: none; }

  .address {
    position: absolute;
    bottom: 48px;
    left: 0; right: 0;
    text-align: center;
    color: var(--white);
    font-size: 15px;
    letter-spacing: 0.3px;
  }

  .back-pattern {
    position: absolute;
    inset: 0;
    background: radial-gradient(circle at 75% 25%, var(--pattern), var(--card-deep) 75%);
  }
  .back-brand {
    position: absolute;
    right: 36px;
    bottom: 50px;
    display: flex;
    align-items: center;
    gap: 6px;
  }
  .back-brand .brand-mark { width: 14px; height: 14px; border-radius: 3px; }
  .back-brand .brand-name { font-size: 12px; letter-spacing: 0.5px; }
</style>
</head>
<body>
  <section class="card card-front">
    <div class="brand">
      <span class="brand-mark"></span>
      <span class="brand-name">HARLOW BUILDERS</span>
    </div>

    <div class="details">
      <div class="person">
        <div class="person-name">MARCUS ELLERY</div>
        <div class="person-role">Managing Director</div>
      </div>
      <div class="divider"></div>
      <ul class="contacts">
        <li>
          <svg viewBox="0 0 24 24"><path d="M6.6 10.8a15 15 0 0 0 6.6 6.6l2.2-2.2a1 1 0 0 1 1-.25 11.4 11.4 0 0 0 3.6.57 1 1 0 0 1 1 1V20a1 1 0 0 1-1 1A17 17 0 0 1 3 4a1 1 0 0 1 1-1h3.5a1 1 0 0 1 1 1c0 1.25.2 2.45.57 3.57a1 1 0 0 1-.25 1z"/></svg>
          0491 555 207
        </li>
        <li>
          <svg viewBox="0 0 24 24"><path d="M2 5h20v14H2z M4 7v.5l8 5 8-5V7l-8 5z" fill-rule="evenodd"/></svg>
          info@harlowbuilders.com
        </li>
        <li>
          <svg viewBox="0 0 24 24"><circle cx="12" cy="12" r="10"/></svg>
          www.harlowbuilders.com
        </li>
      </ul>
    </div>

    <p class="address">1450 W Cedar Avenue Milford County Name 5120</p>
  </section>

  <section class="card card-back">
    <div class="back-pattern" role="img" aria-label="Repeating faint brand pattern across the card back"></div>
    <div class="back-brand">
      <span class="brand-mark"></span>
      <span class="brand-name">HARLOW BUILDERS</span>
    </div>
  </section>
</body>
</html>
```